Wine Label Design-Hollow Creek Vineyard

Hollow Creek Vineyard is in the Barossa Valley in South Australia. The Barossa is recognized as Australia's premier wine region, producing Australia's icon wines and some " new takes on traditional".
This family owned and operated vineyard grows some exceptionally high quality fruit. Most of the fruit is sold and used for some of Australia's most iconic wines. Small quantities are retained by the owners for some wines with very limited availability. (Wines were previously sold as Brackwell Vineyards Hollow Creek ( Shiraz, Cabernet etc).

The wines will in the future be labeled simply ‘Hollow Creek Vineyard’. The label will launch this new identity for the single family single vineyard and its high quality wines which are a true expression of the vineyard and derive from the Hollow Creek common to this ancient area (800-2000 million years old).
The label should reflect
• Single vineyard, family owned
• vines in very old rock & soils
• High quality & reliability
• Edgy but true, design based thinking (Please note:blue is generally seen as an unacceptable colour for a wine label?? Don’t ask me why)

The wines will be sold mostly direct in Australia ( ie not through retail stores), with limited export to Asia, Scandinavia and Canada.
There are three quality levels and price points in the portfolio
1. Entry level premium for everyday drinking for discriminating drinkers-approx AUD20
2. Super Premium-approx AUD30
3. Limited Release ultlra premium-AUD75-90?
We envisage three variations on the label but with an obvious & common design element. This design element should be able to be used for corporate identification and promotion
The paper stock will be waterproof and self adhesive. Our preference is for designs that engage the user by appealing to both sight and touch. It is preferred that textures be added eg embossing, high build varnish etc-rather than be a facet of the stock itself.
For information on statutory label requirements refer to www.vintnerregistry-example.com . In brief
o Front label need not show any mandatory information. However we would prefer Variety, Barossa Valley, Year and alcohol to be shown on the front label
o Back label should show all mandatories and allow for a bar code
Updates

Project Deadline Extended
Reason: I've had a problem with my wireless broadband account and reception has been intermittent to say the least to the extent that I switched off at the weekend. Just going downtown now for a 'polite discussion' with my service provider.

Project Deadline Extended
Reason: I have receiver insufficient designs of quality which we would consider. Too many designs have a "cut and paste" appearance - too few exhibit an original art/design element which truly identifies the product.

Gals & Guys

most of the designs submitted lack punch and originality and are totally unmemorable.
Please-get on Searcho or whatever enter "Wine Label Designs" and do some research b4 u waste your time and mine. Formulaic cut and paste will not win the day. That's not to say that cut and paste can't work-but it must have some originality, impact and command attention. Please surprise me.

Following on from a question from a designer about who is our competition and what we are looking for I sent the following 
"I don't think I can add anything new. Read the brief and comments again and research wine labels on the web. In 30 minutes you'll get a good idea of the creative edgy designs in the industry. There are a plethora of collections. Our competition-anyone with a label. In 2010 there were over 2400 "producers" in other words 2400 producers with at least one label. In fact there are over 25000 Australian wines and then the numerous imported wines.

Target Market(s)

$20 people who budget everyday but have graduated from drinking 'entry level' wines. These people will likely fit into Cat. (b) in the $30 wine

$30 (a) will not over-compromise on some everyday discretionary expenditure.(b) might buy for special occasions

$70-$90 Professional/successful people with high disposable/discretionary income not particularly worried about recession. wine geeks.

Industry/Entity Type

Retail

Requirements
Must have
• identifiable element across range of wines

```html
<!DOCTYPE html>
<html lang="en">
<head>
<meta charset="utf-8">
<title>Hollow Creek – Shiraz Barossa Valley 2012</title>
<link rel="stylesheet" href="https://fonts.googleapis.com/css2?family=Josefin+Sans:wght@400;600&family=Pinyon+Script&display=swap">
<style>
  :root {
    --stage-top: #5c5c5c;
    --stage-bottom: #8a8a8a;
    --linen: #dcd7d1;
    --ink: #151515;
    --paper-text: #d9d4ce;
    --tag-bg: #000000;
    --tag-text: #ffffff;
  }
  * { box-sizing: border-box; margin: 0; padding: 0; }
  html, body {
    width: 1200px;
    height: 837px;
    overflow: hidden;
  }
  body {
    position: relative;
    background: linear-gradient(180deg, var(--stage-top) 0%, var(--stage-bottom) 100%);
    font-family: "Josefin Sans", sans-serif;
  }
  .range-tag {
    position: absolute;
    left: 0;
    top: 56px;
    width: 243px;
    height: 18px;
    background: var(--tag-bg);
    color: var(--tag-text);
    font-family: "Josefin Sans", sans-serif;
    font-weight: 600;
    font-size: 13px;
    letter-spacing: 3.6px;
    line-height: 19px;
    padding-left: 20px;
  }
  .label-panel {
    position: absolute;
    left: 450px;
    top: 34px;
    width: 300px;
    height: 770px;
    background: var(--linen);
  }
  .pattern-field {
    position: absolute;
    left: 8px;
    top: 118px;
    width: 284px;
    height: 502px;
    border-radius: 142px / 251px;
    background: radial-gradient(ellipse at center, rgba(21,21,21,0.55) 0%, rgba(21,21,21,0.35) 55%, rgba(21,21,21,0.12) 80%, rgba(21,21,21,0) 100%);
  }
  .disc {
    position: absolute;
    left: 47px;
    width: 206px;
    height: 206px;
    border-radius: 50%;
    display: flex;
    flex-direction: column;
    align-items: center;
    justify-content: center;
    text-align: center;
  }
  .disc--variety { top: 103px; background: var(--ink); color: var(--paper-text); }
  .disc--name    { top: 253px; background: var(--linen); color: var(--ink); }
  .disc--origin  { top: 413px; background: var(--ink); color: var(--paper-text); }
  .variety-line {
    font-size: 14px;
    letter-spacing: 3.4px;
    line-height: 22px;
  }
  .variety-line--region { letter-spacing: 2.8px; }
  .disc--variety .variety-line:first-child { margin-top: 18px; }
  .wine-name {
    font-family: "Josefin Sans", sans-serif;
    font-weight: 400;
    font-size: 22px;
    letter-spacing: 1px;
    line-height: 28px;
    margin-top: 4px;
  }
  .origin-script {
    font-family: "Pinyon Script", cursive;
    font-size: 21px;
    line-height: 24px;
    margin-top: -14px;
  }
  .vintage {
    font-size: 13px;
    letter-spacing: 3px;
    margin-top: 4px;
  }
</style>
</head>
<body>
  <div class="range-tag">LIMITED RELEASE</div>

  <section class="label-panel" aria-label="Hollow Creek Shiraz front label">
    <div class="pattern-field" role="img" aria-label="Fine black spirograph line pattern framing the three stacked circles"></div>

    <div class="disc disc--variety">
      <p class="variety-line">SHIRAZ</p>
      <p class="variety-line variety-line--region">BARROSA VALLEY</p>
    </div>

    <div class="disc disc--name">
      <h1 class="wine-name">HOLLOW<br>CREEK</h1>
    </div>

    <div class="disc disc--origin">
      <p class="origin-script">Wine Of Australia</p>
      <p class="vintage">2012</p>
    </div>
  </section>
</body>
</html>
```